Veranix - Solution provider in business consulting

Veranix is a swiss based company providing solutions for developing markets. The business covers various fields of business consulting, such as supply chain, product costs, quality management and manufacturing management. The Business operates in a efficient, straight and solution oriented manner.
The final design should communicate these characteristics. Asian people as well as as western people shall identify the qualities of the company at first sight.
The customer needs business cards with a simple view but an recognizable design, printed in high quality. Engraved elements such as the globe or simple words are possible.
Available colors are: (RAL)
102/102/102
51/102/102
153/204/153
255/102/51
Font: Calibri

```html
<!DOCTYPE html>
<html lang="en">
<head>
<meta charset="utf-8">
<title>Veranix — Business Card</title>
<link rel="stylesheet" href="https://fonts.googleapis.com/css2?family=Carlito:wght@400;700&display=swap">
<style>
  :root {
    --page-bg: #e9e9e7;
    --card-bg: #fbfbfb;
    --card-edge: #f1f1f1;
    --ink-dark: #666666;
    --ink-mid: #7a7a7a;
    --ink-soft: #9a9a9a;
    --rule: #8c8c8c;
    --globe-light: #f0f0f0;
    --globe-shade: #e2e2e2;
  }
  * { margin: 0; padding: 0; box-sizing: border-box; }
  html, body {
    width: 1200px; height: 1022px; overflow: hidden;
    background: var(--page-bg);
    font-family: "Carlito", "Calibri", sans-serif;
  }
  .stage {
    width: 1200px; height: 1022px;
    display: flex; align-items: center; justify-content: center;
  }
  .business-card {
    position: relative;
    width: 900px; height: 514px;
    border-radius: 22px;
    background: linear-gradient(135deg, #ffffff 0%, var(--card-bg) 55%, var(--card-edge) 100%);
    box-shadow: 0 18px 40px rgba(0,0,0,0.18), 0 2px 6px rgba(0,0,0,0.12);
    overflow: hidden;
  }
  .globe-backdrop {
    position: absolute;
    right: -150px; top: -40px;
    width: 600px; height: 600px;
    border-radius: 50%;
    background: radial-gradient(circle at 40% 40%, var(--globe-light) 0%, var(--globe-shade) 100%);
    opacity: 0.7;
  }
  .brand {
    position: absolute;
    left: 80px; top: 50%;
    transform: translateY(-50%);
    display: flex; align-items: center; gap: 22px;
  }
  .brand-dot {
    width: 64px; height: 64px; border-radius: 50%;
    background: var(--ink-dark);
  }
  .brand-name {
    font-size: 112px; font-weight: 400;
    color: var(--ink-dark);
    letter-spacing: 2px; line-height: 1;
  }
  .divider {
    position: absolute;
    left: 520px; top: 128px;
    width: 1px; height: 258px;
    background: var(--rule);
  }
  .contact {
    position: absolute;
    left: 548px; top: 128px;
    color: var(--ink-mid);
  }
  .contact-name {
    font-size: 34px; font-weight: 700; color: var(--ink-dark); line-height: 1.05;
  }
  .contact-role { font-size: 21px; margin-bottom: 22px; }
  .contact-address { font-size: 21px; line-height: 1.3; margin-bottom: 14px; }
  .contact-list { list-style: none; font-size: 21px; line-height: 1.35; }
  .contact-list li { display: flex; align-items: center; gap: 12px; }
  .contact-icon { width: 16px; height: 16px; flex: none; }
</style>
</head>
<body>
<main class="stage">
  <section class="business-card">
    <div class="globe-backdrop" role="img" aria-label="Faint world map globe in the background"></div>

    <div class="brand">
      <span class="brand-name">Veranix</span>
      <span class="brand-dot"></span>
    </div>

    <div class="divider"></div>

    <div class="contact">
      <p class="contact-name">Marco Weiler</p>
      <p class="contact-role">CEO</p>
      <p class="contact-address">Veranix GmbH Talweg<br>14 9310 Hinterau Switzerland</p>
      <ul class="contact-list">
        <li>
          <svg class="contact-icon" viewBox="0 0 16 16" aria-hidden="true"><rect x="4" y="1" width="8" height="14" rx="1.5" fill="none" stroke="#666" stroke-width="1.5"/><circle cx="8" cy="12.5" r="0.9" fill="#666"/></svg>
          +41 79 555 0142
        </li>
        <li>
          <svg class="contact-icon" viewBox="0 0 16 16" aria-hidden="true"><path d="M4 1.5 L6.5 4.5 L5 6.5 C6 8.5 7.5 10 9.5 11 L11.5 9.5 L14.5 12 L13 14.5 C7 14 2 9 1.5 3 Z" fill="#666"/></svg>
          +41 71 555 0187
        </li>
        <li>
          <svg class="contact-icon" viewBox="0 0 16 16" aria-hidden="true"><rect x="1.5" y="3.5" width="13" height="9" fill="none" stroke="#666" stroke-width="1.5"/><path d="M1.5 3.5 L8 9 L14.5 3.5" fill="none" stroke="#666" stroke-width="1.5"/></svg>
          marco.weiler@veranix.ch
        </li>
        <li>
          <svg class="contact-icon" viewBox="0 0 16 16" aria-hidden="true"><circle cx="8" cy="8" r="6.5" fill="none" stroke="#666" stroke-width="1.5"/><ellipse cx="8" cy="8" rx="2.8" ry="6.5" fill="none" stroke="#666" stroke-width="1.2"/><path d="M1.5 8 H14.5" stroke="#666" stroke-width="1.2"/></svg>
          www.veranix.ch
        </li>
      </ul>
    </div>
  </section>
</main>
</body>
</html>
```